Stylish new business card needed!

Hello everyone! I am in need of a new business card design for an alarm company here in Hurricane WV. I have all fonts, color codes and logos provided for you use! We are a young company and like the style of a clean sleek looking business card. Would like it double sided, one side holding the logo and the other with your design!
Target Market(s)
The people that are looking for the newest tech for home automation and security
Industry/Entity Type
Alarm services; Home automation
Contact Information for Business Card
Name of person; position (Sales; Installer); Phone Number (555.418.7260); Employee cell Number; Website (www.GuardedByVelk.example); Employee Email; Double sided
Look and feel
Each slider illustrates characteristics of the customer's brand and the style your logo design should communicate.

```html
<!DOCTYPE html>
<html lang="en">
<head>
<meta charset="utf-8">
<title>Velk Business Card</title>
<link href="https://fonts.googleapis.com/css2?family=Lato:wght@400;700;900&display=swap" rel="stylesheet">
<style>
  :root {
    --backdrop: #1b1b1b;
    --card: #2a2a2a;
    --card-edge: #f58a4b;
    --accent: #f58a4b;
    --text-light: #d6d6d6;
    --text-muted: #b4b4b4;
    --divider: #555555;
  }
  * { margin: 0; padding: 0; box-sizing: border-box; }
  html, body {
    width: 1200px;
    height: 939px;
    overflow: hidden;
    background: var(--backdrop);
    font-family: "Lato", sans-serif;
  }
  .stage {
    width: 1200px;
    height: 939px;
    display: flex;
    flex-direction: column;
    align-items: center;
    justify-content: center;
    gap: 60px;
  }
  .card {
    width: 600px;
    height: 343px;
    background: var(--card);
    border-radius: 22px;
    border-bottom: 3px solid var(--card-edge);
    border-left: 2px solid var(--card-edge);
    position: relative;
    overflow: hidden;
  }
  /* Front: brand name */
  .card-front {
    display: flex;
    align-items: center;
    justify-content: center;
  }
  .brand {
    display: flex;
    align-items: center;
    gap: 18px;
  }
  .brand-dot {
    width: 30px;
    height: 30px;
    border-radius: 50%;
    background: var(--accent);
  }
  .brand-name {
    font-weight: 400;
    font-size: 92px;
    letter-spacing: 4px;
    color: var(--text-light);
    line-height: 1;
  }
  /* Back: contact details */
  .card-back {
    display: flex;
    align-items: center;
    padding: 0 40px 0 70px;
  }
  .identity {
    width: 235px;
    text-align: right;
    padding-right: 26px;
  }
  .person-name {
    font-weight: 900;
    font-size: 28px;
    color: var(--accent);
    letter-spacing: 0.3px;
    line-height: 1.05;
  }
  .person-role {
    font-size: 18px;
    color: var(--text-muted);
    margin-top: 2px;
  }
  .divider {
    width: 1px;
    height: 150px;
    background: var(--divider);
  }
  .contact-list {
    list-style: none;
    padding-left: 26px;
    font-size: 15px;
    color: var(--text-light);
    line-height: 1.45;
  }
  .contact-list li {
    display: flex;
    align-items: flex-start;
    gap: 10px;
  }
  .contact-list svg {
    width: 12px;
    height: 12px;
    margin-top: 5px;
    flex-shrink: 0;
    fill: var(--accent);
  }
</style>
</head>
<body>
<main class="stage">
  <section class="card card-front" aria-label="Card front">
    <div class="brand">
      <span class="brand-dot"></span>
      <span class="brand-name">VELK</span>
    </div>
  </section>

  <section class="card card-back" aria-label="Card back">
    <div class="identity">
      <p class="person-name">DANIEL REYES</p>
      <p class="person-role">Sales &amp; Installer</p>
    </div>
    <div class="divider"></div>
    <ul class="contact-list">
      <li>
        <svg viewBox="0 0 12 12"><path d="M6 0a4 4 0 0 0-4 4c0 3 4 8 4 8s4-5 4-8a4 4 0 0 0-4-4zm0 5.6A1.6 1.6 0 1 1 6 2.4a1.6 1.6 0 0 1 0 3.2z"/></svg>
        <span>Address, City, State<br>Country, Zip Code 01235</span>
      </li>
      <li>
        <svg viewBox="0 0 12 12"><path d="M2.5 0.5l2 2.2-1 1.3c.7 1.6 2 2.9 3.5 3.6l1.3-1 2.2 2-1.1 2.2C5 10.5 1.5 7 .3 1.6z"/></svg>
        <span>555.418.7260</span>
      </li>
      <li>
        <svg viewBox="0 0 12 12"><path d="M3 0h6v12H3zm1 1.5v8h4v-8zm2 8.7a.6.6 0 1 0 0 1.2.6.6 0 0 0 0-1.2z"/></svg>
        <span>555.418.7391</span>
      </li>
      <li>
        <svg viewBox="0 0 12 12"><path d="M0 2h12v8H0zm1 1v.4l5 3.2 5-3.2V3z"/></svg>
        <span>daniel@guardedbyvelk.example</span>
      </li>
      <li>
        <svg viewBox="0 0 12 12"><path d="M6 0a6 6 0 1 0 0 12A6 6 0 0 0 6 0zm0 1.2c.6.8 1 2 1.1 3.3H4.9C5 3.2 5.4 2 6 1.2zM1.3 5.5h2.5c0 1.3.4 2.6.9 3.5a4.8 4.8 0 0 1-3.4-3.5zm3.6 0h2.2c-.1 1.3-.5 2.5-1.1 3.3-.6-.8-1-2-1.1-3.3zm3.3 0h2.5a4.8 4.8 0 0 1-3.4 3.5c.5-.9.9-2.2.9-3.5zm2.5-1H8.2c0-1.3-.4-2.6-.9-3.5a4.8 4.8 0 0 1 3.4 3.5zM4.7 1c-.5.9-.9 2.2-.9 3.5H1.3A4.8 4.8 0 0 1 4.7 1z"/></svg>
        <span>GuardedByVelk.example</span>
      </li>
    </ul>
  </section>
</main>
</body>
</html>
```